Brenlow Estates Website and Logo Design

We need a new logo and website designed for 'Brenlow Estates Ltd', which is a well established Guernsey property holding company founded in 1934.

The company does not currently have a website. The new website should be similar in style and layout to https://www.quorvanhall.example/.

Target Market(s)

Industry, Media, Tenants

Industry/Entity Type

Property Management

Logo Text

BEL OR Brenlow Estates Ltd OR BE

Coding

Coded - Design and coding required

Number of Pages Required

4 page

Font styles to use
Other font styles liked:
• Helvetica

Requirements
Must have
• The logo laying over the picture (like https://www.quorvanhall.example/).
• Big pictures on homepage (like https://www.quorvanhall.example/)

```html
<!DOCTYPE html>
<html lang="en">
<head>
<meta charset="utf-8">
<title>Brenlow Estates Limited</title>
<link rel="stylesheet" href="https://fonts.googleapis.com/css2?family=Montserrat:wght@400;600;700&family=Open+Sans:ital,wght@0,400;0,600;1,400&display=swap">
<style>
:root{
  --blue:#4a7bd0;
  --blue-dark:#2f5fa8;
  --ink:#3d3d3d;
  --muted:#777;
  --light-bg:#f4f4f5;
  --footer-bg:#f5f5f6;
  --bar:#3a3a3a;
  --grey-btn:#676767;
  --white:#fff;
}
*{margin:0;padding:0;box-sizing:border-box}
html,body{width:684px;height:1200px;overflow:hidden;background:var(--white)}
body{position:relative;font-family:Arial,Helvetica,sans-serif;color:var(--muted)}
.abs{position:absolute}
.head-font{font-family:'Montserrat',Arial,sans-serif}

/* hero */
.hero{left:0;top:0;width:684px;height:355px;overflow:hidden}
.hero-photo{position:absolute;inset:0;background:linear-gradient(180deg,#5a78b8 0%,#7c9acd 18%,#a8a39a 32%,#8a8277 42%,#3f6e86 55%,#2f5f72 75%,#3b6b7a 100%)}
.hero-shade{position:absolute;inset:0;background:linear-gradient(180deg,rgba(20,30,60,.35),rgba(0,0,0,0) 25%,rgba(0,0,0,.1))}
.brand{left:49px;top:26px;font-family:'Montserrat',Arial,sans-serif;font-weight:600;font-size:14px;color:var(--white);letter-spacing:.2px}
.nav{top:30px;font-family:'Montserrat',Arial,sans-serif;font-weight:600;font-size:7px;color:var(--white)}
.hero-title{left:0;width:684px;top:204px;text-align:center;font-family:'Montserrat',Arial,sans-serif;font-size:19px;font-weight:400;color:var(--white);letter-spacing:.3px}
.hero-text{left:150px;width:384px;top:237px;text-align:center;font-size:7px;line-height:14px;color:var(--white)}
.hero-btn{left:289px;top:278px;width:106px;height:25px;background:var(--blue);border-radius:2px;color:var(--white);font-family:'Montserrat',Arial,sans-serif;font-weight:600;font-size:8px;display:flex;align-items:center;justify-content:center}
.dots{left:328px;top:337px;display:flex;gap:6px}
.dots span{width:6px;height:6px;border-radius:50%;background:var(--white)}
.dots span.on{background:var(--blue)}

/* welcome */
.welcome-title{left:0;width:684px;top:377px;text-align:center;font-family:'Montserrat',Arial,sans-serif;font-weight:600;font-size:12.5px;color:var(--blue)}
.welcome-text{left:145px;width:394px;top:407px;text-align:center;font-size:6.6px;line-height:14.4px;color:var(--muted)}
.btn-solid{height:21px;border-radius:2px;color:var(--white);font-family:'Montserrat',Arial,sans-serif;font-weight:600;font-size:7px;display:flex;align-items:center;justify-content:center}

/* features */
.features{left:0;top:520px;width:684px;height:278px;background:var(--light-bg)}
.col-title{top:547px;font-family:'Montserrat',Arial,sans-serif;font-weight:600;font-size:9px;color:var(--ink)}
.col-photo{top:569px;width:188px;height:120px;border:1px solid #ddd;background:var(--white);padding:2px}
.col-photo div{width:100%;height:100%}
.col-text{top:700px;width:192px;font-size:6.4px;line-height:14.4px;color:var(--muted)}
.btn-outline{height:23px;border:1px solid var(--blue);border-radius:2px;background:var(--white);color:var(--blue-dark);font-family:'Montserrat',Arial,sans-serif;font-weight:600;font-size:6.5px;display:flex;align-items:center;justify-content:center}

/* about + testimonial */
.sec-title{font-family:'Montserrat',Arial,sans-serif;font-weight:600;font-size:11px;color:#555}
.about-text{left:50px;top:854px;width:284px;font-size:6.6px;line-height:15.2px;color:var(--muted)}
.avatar{left:362px;top:858px;width:72px;height:72px;border-radius:50%;background:radial-gradient(circle at 50% 45%,#c9a18a,#7a5a48 70%,#4a3a33)}
.quote{font-family:Georgia,serif;font-size:14px;color:#666;font-weight:700}
.quote-text{left:455px;top:873px;width:184px;font-size:6.3px;line-height:13.3px;color:var(--muted)}
.t-name{left:456px;top:962px;font-family:'Open Sans',Arial,sans-serif;font-weight:600;font-size:7.6px;color:var(--blue-dark)}
.t-date{left:456px;top:975px;font-family:'Open Sans',Arial,sans-serif;font-style:italic;font-size:5.6px;color:var(--muted)}

/* footer */
.footer{left:0;top:1008px;width:684px;height:154px;background:var(--footer-bg)}
.f-title{top:1041px;font-family:'Montserrat',Arial,sans-serif;font-weight:600;font-size:8px;color:#444}
.f-links{left:58px;top:1059px;list-style:none;font-family:'Open Sans',Arial,sans-serif;font-size:7px;color:#666}
.f-links li{height:15.2px;display:flex;align-items:center}
.f-links li::before{content:"»";margin-right:11px;color:#888;font-size:8px}
.contact{left:188px;top:1064px;font-size:6.4px;color:#777}
.contact .row{display:flex;gap:8px;align-items:flex-start;margin-bottom:8px;line-height:8px}
.contact svg{width:8px;height:8px;flex:none;fill:#888}
.nl-text{left:356px;top:1063px;width:130px;font-family:'Open Sans',Arial,sans-serif;font-size:6.4px;line-height:10.8px;color:#777}
.nl-input{left:356px;top:1094px;width:121px;height:19px;background:var(--white);border:1px solid #ccc;font-family:'Open Sans',Arial,sans-serif;font-size:6.4px;color:#555;padding-left:8px;display:flex;align-items:center}
.nl-btn{left:357px;top:1119px;width:45px;height:15px;background:var(--blue);color:var(--white);font-family:'Open Sans',Arial,sans-serif;font-size:5.6px;font-weight:600;display:flex;align-items:center;justify-content:center}
.follow-text{left:505px;top:1065px;width:120px;font-family:'Open Sans',Arial,sans-serif;font-size:5.6px;line-height:10.6px;color:#888}
.socials{left:503px;top:1107px;display:flex;gap:4px}
.socials span{width:20px;height:20px;border-radius:50%;border:1px solid #999}
.bar{left:0;top:1162px;width:684px;height:38px;background:var(--bar);color:var(--white);font-size:7.4px;display:flex;align-items:center;justify-content:center}
</style>
</head>
<body>

<section class="abs hero">
  <div class="hero-photo" role="img" aria-label="Harbour town with moored boats, waterfront houses and blue sky"></div>
  <div class="hero-shade"></div>
</section>
<div class="abs brand">BRENLOW ESTATES LIMITED</div>
<nav>
  <span class="abs nav" style="left:340px">HOME</span>
  <span class="abs nav" style="left:395px">ABOUT US</span>
  <span class="abs nav" style="left:466px">SERVICES</span>
  <span class="abs nav" style="left:534px">NEWS</span>
  <span class="abs nav" style="left:588px">CONTACT US</span>
</nav>
<h1 class="abs hero-title">BRENLOW ESTATES LIMITED</h1>
<p class="abs hero-text">Sed ut perspiciatis unde omnis iste natus error sit voluptatem accusantium doloremque laudantium, totam rem illo inventore veritatis et quasi architecto beatae vitae dicta sunt explicabo.</p>
<div class="abs hero-btn">READ MORE INFO</div>
<div class="abs dots"><span></span><span class="on"></span><span></span></div>

<h2 class="abs welcome-title">WELCOME TO OUR COMPANY</h2>
<p class="abs welcome-text">Sed ut perspiciatis unde omnis iste natus error sit voluptatem accusantium doloremque laudantium, totam rem aperiam, eaque ipsa quae ab illo inventore veritatis et quasi architecto beatae vitae dicta sunt explicabo. Nemo enim ipsam voluptatem quia sed quia consequuntur magni dolores eos qui ratione voluptatem sequi nesciunt.</p>
<div class="abs btn-solid" style="left:269px;top:466px;width:71px;background:var(--blue)">LEARN MORE</div>
<div class="abs btn-solid" style="left:344px;top:466px;width:71px;background:var(--grey-btn)">OUR FEATURED</div>

<section class="abs features"></section>
<h3 class="abs col-title" style="left:49px">WHAT WE DO</h3>
<h3 class="abs col-title" style="left:248px">HOW IT WORKS</h3>
<h3 class="abs col-title" style="left:447px">WHY CHOOSE US</h3>
<div class="abs col-photo" style="left:49px"><div role="img" aria-label="Sea view with headland and small boats by a pier" style="background:linear-gradient(180deg,#7d9cc8 0%,#b4c3d6 35%,#5f7d78 45%,#2f6f75 70%,#3a5f66 100%)"></div></div>
<div class="abs col-photo" style="left:248px"><div role="img" aria-label="Bay with rocky island and moored boats" style="background:linear-gradient(180deg,#5d8ad0 0%,#9fbbe0 40%,#5c6a55 50%,#2c5a93 62%,#2a4f86 100%)"></div></div>
<div class="abs col-photo" style="left:447px"><div role="img" aria-label="Harbour marina in front of a hillside town" style="background:linear-gradient(180deg,#5f82c6 0%,#98b0d8 30%,#9c9890 50%,#6c7480 65%,#3b5b78 100%)"></div></div>
<p class="abs col-text" style="left:49px">Sed ut perspiciatis unde omnis iste natus error sit voluptatem accusantium doloremque laudantium, totam rem aperiam,bea tae vitae dicta sunt explicabo.</p>
<p class="abs col-text" style="left:248px">Sed ut perspiciatis unde omnis iste natus error sit voluptatem accusantium doloremque laudantium, totam rem aperiam,bea tae vitae dicta sunt explicabo.</p>
<p class="abs col-text" style="left:447px">Sed ut perspiciatis unde omnis iste natus error sit voluptatem accusantium doloremque laudantium, totam rem aperiam,bea tae vitae dicta sunt explicabo.</p>
<div class="abs btn-outline" style="left:49px;top:751px;width:68px">LEARN MORE</div>
<div class="abs btn-outline" style="left:248px;top:751px;width:68px">LEARN MORE</div>
<div class="abs btn-outline" style="left:447px;top:751px;width:68px">LEARN MORE</div>

<h2 class="abs sec-title" style="left:50px;top:825px">ABOUT US</h2>
<p class="abs about-text">Sed ut perspiciatis unde omnis iste natus error sit voluptatem accusantium doloremque laudantium, totam rem aperiam, eaque ipsa quae ab illo inventore veritatis et quasi architecto beatae vitae dicta sunt explicabo. Nemo enim ipsam voluptatem quia voluptas sit aspernatur aut odit aut fugit, sed quia consequuntur magni dolores eos qui ratione voluptatem sequi nesciunt. consequuntur magni dolores eos qui ratione voluptatem sequi nesciunt. Neque porro quisquam est, qui dolorem ipsum</p>
<div class="abs btn-outline" style="left:50px;top:961px;width:71px">READ MORE</div>

<h2 class="abs sec-title" style="left:362px;top:823px">TESTIMONIALS</h2>
<div class="abs avatar" role="img" aria-label="Client portrait photo"></div>
<span class="abs quote" style="left:445px;top:862px">“</span>
<p class="abs quote-text">Sed ut perspiciatis unde omnis iste natus error sit volupta tem accusantium doloremque laudantium, totam rem aperi am, eaque ipsa quae ab illo inventore veritatis et quasi arch tecto beatae vitae dicta sunt explicabo. Nemo enim ipsam voluptatem quia voluptas sit aspernatur aut odit aut ratione voluptatem sequi nesciunt</p>
<span class="abs quote" style="left:544px;top:939px">”</span>
<div class="abs t-name">Name : Mara Ellison</div>
<div class="abs t-date">Posted on 02 November 2016</div>

<footer class="abs footer"></footer>
<h4 class="abs f-title" style="left:58px">QUICK LINKS</h4>
<h4 class="abs f-title" style="left:188px">CONTACT US</h4>
<h4 class="abs f-title" style="left:356px">NEWSLETTER</h4>
<h4 class="abs f-title" style="left:505px">FOLLOW US</h4>
<ul class="abs f-links">
  <li>Home</li><li>About us</li><li>Services</li><li>News</li><li>Contact us</li>
</ul>
<div class="abs contact">
  <div class="row"><svg viewBox="0 0 10 10"><path d="M1 3c0-1 1-2 4-2s4 1 4 2v1H7V3H3v1H1zM2 5h6l1 4H1z"/></svg><span>(000)-555-0142 (Phone)</span></div>
  <div class="row"><svg viewBox="0 0 10 10"><rect x="3" y="1" width="4" height="3"/><rect x="1" y="4" width="8" height="4" rx="1"/><rect x="3" y="7" width="4" height="2"/></svg><span>(000)-555-0143 (Fax)</span></div>
  <div class="row"><svg viewBox="0 0 10 10"><path d="M1 2h8v6H1zM1 2l4 3 4-3" fill="none" stroke="#888"/></svg><span style="text-decoration:underline">info@brenlowestates.example</span></div>
  <div class="row"><svg viewBox="0 0 10 10"><path d="M5 0a3 3 0 0 1 3 3c0 2-3 6-3 6S2 5 2 3a3 3 0 0 1 3-3z"/></svg><span>#123 lorem Ipsum Dummy Text<br>Lorem Ipsum</span></div>
</div>
<p class="abs nl-text">Register Your email address to get information ablout us</p>
<div class="abs nl-input">Email Address</div>
<div class="abs nl-btn">SUBSCRIBE</div>
<p class="abs follow-text">Lorem ipsum dolor sit amet, conse ctetur adipiscing elit. Nulla in purus nibh. Donec ornare</p>
<div class="abs socials"><span></span><span></span><span></span><span></span><span></span></div>
<div class="abs bar">© Copyright 2016 Brenlow Estates Limited.All Rights Reserved</div>

</body>
</html>
```